Verodex business card

Business card for sustainable investment company called "Verodex". Verodex is an exchange platform selling carbon credits between buyers and sellers. Carbon Credits are an environmental commodity for reducing global carbon emissions.

the card should obviously have our logo and the theme should be sustainability/environment mixed with a trading platform.

Contact Information for Business Card

Logo, Name, Title, Phone, Email

Colors
0054AA
0677BA
7BADD7
CADEEF
E8F1F8
0094D4
00A9DD
6FCCEA
C7EBF8
E9F6FB
00AB8E
00BBA5
67D7C9
C6EFE9
E9F9F6
59FF00
82FF00
B8FF75
E3FFCB
F4FFEA

```html
<!DOCTYPE html>
<html lang="en">
<head>
<meta charset="UTF-8">
<title>Verodex Business Card</title>
<link rel="stylesheet" href="https://fonts.googleapis.com/css2?family=Montserrat:wght@400;500;600;700&display=swap">
<style>
  :root {
    --stage-bg: #2a2b2e;
    --card-dark: #0b0c0f;
    --card-mid: #1d1f23;
    --brand-blue: #0094d4;
    --accent-blue: #4fa8dc;
    --text-light: #ffffff;
    --text-soft: #e6e9ee;
  }
  * { box-sizing: border-box; margin: 0; padding: 0; }
  html, body {
    width: 1200px;
    height: 900px;
    overflow: hidden;
    background: var(--stage-bg);
    font-family: "Montserrat", sans-serif;
  }
  .stage {
    width: 1200px;
    height: 900px;
    display: flex;
    flex-direction: column;
    align-items: center;
    justify-content: center;
    gap: 40px;
  }
  .card {
    width: 700px;
    height: 400px;
    position: relative;
    background: linear-gradient(125deg, var(--card-dark) 0%, var(--card-mid) 100%);
    box-shadow: 0 10px 30px rgba(0,0,0,0.45);
    overflow: hidden;
  }
  .brand {
    display: flex;
    align-items: center;
    gap: 18px;
  }
  .brand-mark {
    width: 44px;
    height: 44px;
    background: var(--brand-blue);
  }
  .brand-name {
    color: var(--text-light);
    font-weight: 600;
    letter-spacing: 0.04em;
    text-transform: uppercase;
  }
  .card-front {
    display: flex;
    align-items: center;
    justify-content: center;
  }
  .card-front .brand-name { font-size: 58px; }
  .card-front .brand-mark { width: 58px; height: 58px; }

  .card-back { padding: 44px 52px; }
  .card-back .brand-name { font-size: 42px; }
  .card-back .brand-mark { width: 42px; height: 42px; }

  .person {
    margin-top: 38px;
    display: flex;
    gap: 14px;
    align-items: stretch;
  }
  .person-bar {
    width: 12px;
    background: var(--accent-blue);
  }
  .person-name {
    color: var(--accent-blue);
    font-weight: 700;
    font-size: 26px;
    letter-spacing: 0.05em;
    text-transform: uppercase;
    line-height: 1.1;
  }
  .person-title {
    color: var(--text-soft);
    font-size: 15px;
    letter-spacing: 0.08em;
    text-transform: uppercase;
  }
  .address {
    margin-top: 20px;
    color: var(--text-soft);
    font-size: 15px;
    line-height: 1.45;
    letter-spacing: 0.03em;
    max-width: 380px;
  }
  .contact-list {
    margin-top: 14px;
    list-style: none;
    display: flex;
    flex-direction: column;
    gap: 6px;
  }
  .contact-item {
    display: flex;
    align-items: center;
    gap: 12px;
    color: var(--text-light);
    font-size: 16px;
    letter-spacing: 0.03em;
  }
  .contact-icon { width: 16px; height: 16px; flex: none; }
</style>
</head>
<body>
<main class="stage">
  <section class="card card-front" aria-label="Card front">
    <div class="brand">
      <span class="brand-mark" aria-hidden="true"></span>
      <span class="brand-name">Verodex</span>
    </div>
  </section>

  <section class="card card-back" aria-label="Card back">
    <div class="brand">
      <span class="brand-mark" aria-hidden="true"></span>
      <span class="brand-name">Verodex</span>
    </div>

    <div class="person">
      <span class="person-bar" aria-hidden="true"></span>
      <div>
        <p class="person-name">Daren Kolby</p>
        <p class="person-title">Manager</p>
      </div>
    </div>

    <p class="address">2716 Alder Crest Rd. Harbor Point Blvd Westfield, MN 04517</p>

    <ul class="contact-list">
      <li class="contact-item">
        <svg class="contact-icon" viewBox="0 0 16 16" aria-hidden="true">
          <path d="M3.5 1.5l2.5 0 1 3.5-1.6 1.2c.8 1.8 2.2 3.2 4 4l1.2-1.6 3.4 1v2.5c0 .8-.7 1.4-1.5 1.4C6.8 13.5 2.5 9.2 2.1 3c0-.8.6-1.5 1.4-1.5z" fill="var(--accent-blue)"/>
        </svg>
        555-210-4836
      </li>
      <li class="contact-item">
        <svg class="contact-icon" viewBox="0 0 16 16" aria-hidden="true">
          <rect x="1" y="3" width="14" height="10" fill="var(--accent-blue)"/>
          <path d="M1 3.5l7 5 7-5" fill="none" stroke="var(--card-dark)" stroke-width="1.3"/>
        </svg>
        hello@verodex.com
      </li>
      <li class="contact-item">
        <svg class="contact-icon" viewBox="0 0 16 16" aria-hidden="true">
          <g fill="none" stroke="var(--accent-blue)" stroke-width="1.3">
            <circle cx="8" cy="8" r="6.5"/>
            <ellipse cx="8" cy="8" rx="3" ry="6.5"/>
            <path d="M1.5 8h13M2.5 4.8h11M2.5 11.2h11"/>
          </g>
        </svg>
        www.verodex.com
      </li>
    </ul>
  </section>
</main>
</body>
</html>
```